High-end construction company needs a business card design

We need a modern looking business card that draws people in, is memorable and looks so good people will want to sick it on their fridges.
On the first side what is needed are:
Logo
My name - Tomasz Brelwik
Title - Managing Director
Website - www.varkelt.co.uk
Email - tomasz@varkelt.co.uk
Telephone - 020 5194 6281
Mobile - 07845139072
On the back side was is needed is a list of all the services we provide:
-Kitchen Renovations
-Bathroom Renovations
-House Renovations
-Garage Conversions
-Extensions
-Loft Conversions
-Conservatories
-Carpentry
-Tiling
-Electrical
-Plumbing & Heating
-Bricklaying
-Landscaping
-Decorating
-Plastering
We would like the colours to be the same shades as on the logo with grey or black for the words.
Target Market(s)
Anyone who needs building work done
Contact Information for Business Card
This business card is for a construction company which strives to deliver excellent service and quality.
The look and feel of the card should represent this.
Requirements
Must have
- On the first side what is needed are:
Logo
My name - Tomasz Brelwik
Title - Managing Director
Website - www.varkelt.co.uk
Email - tomasz@varkelt.co.uk
Telephone - 020 5194 6281
Mobile - 07845139072
Nice to have
- Cool looking features

```html
<!DOCTYPE html>
<html lang="en">
<head>
<meta charset="utf-8">
<title>Varkelt Construction – Business Card</title>
<link rel="stylesheet" href="https://fonts.googleapis.com/css2?family=Montserrat:wght@400;500;700;800&display=swap">
<style>
  :root {
    --green: #4c9c3e;
    --green-light: #5fb544;
    --green-dark: #3f8a33;
    --ink: #3a3a3a;
    --paper: #ffffff;
    --backdrop: #e9ebe8;
  }
  * { box-sizing: border-box; margin: 0; padding: 0; }
  html, body { width: 1200px; height: 930px; overflow: hidden; }
  body {
    background: var(--backdrop);
    font-family: "Montserrat", sans-serif;
    position: relative;
  }
  .card {
    position: absolute;
    width: 700px;
    height: 400px;
    border-radius: 22px;
    overflow: hidden;
    box-shadow: 0 10px 30px rgba(0,0,0,.18);
  }

  /* Back side: services */
  .card--back {
    left: 110px; top: 40px;
    background: linear-gradient(135deg, var(--green-light) 0%, var(--green) 55%, var(--green-dark) 100%);
    color: var(--paper);
  }
  .services {
    position: absolute;
    left: 44px; top: 40px;
    list-style: none;
    font-size: 15.5px;
    line-height: 21px;
    font-weight: 500;
  }
  .services li { padding-left: 20px; position: relative; }
  .services li::before {
    content: ""; position: absolute; left: 0; top: 7px;
    width: 8px; height: 8px; border-radius: 50%; background: var(--paper);
  }
  .brand { position: absolute; text-align: left; }
  .brand__name { font-weight: 800; letter-spacing: 2px; line-height: 1; }
  .brand__sub { font-weight: 800; letter-spacing: 3px; line-height: 1; margin-top: 6px; }
  .card--back .brand { left: 330px; top: 150px; }
  .card--back .brand__name { font-size: 62px; }
  .card--back .brand__sub { font-size: 16.5px; }

  /* Front side: contact */
  .card--front {
    left: 390px; top: 490px;
    background: var(--paper);
    color: var(--ink);
  }
  .card--front .brand { left: 52px; top: 130px; color: var(--green-light); }
  .card--front .brand__name { font-size: 52px; }
  .card--front .brand__sub { font-size: 14px; }
  .tab {
    position: absolute; right: 0; top: 58px;
    width: 9px; height: 38px; background: var(--green-light);
  }
  .person { position: absolute; right: 40px; top: 52px; text-align: right; }
  .person__name { font-size: 27px; font-weight: 700; color: var(--green-light); }
  .person__title { font-size: 16px; font-weight: 500; margin-top: 2px; }
  .rule { position: absolute; height: 1.5px; background: var(--green-light); }
  .rule--name { right: 20px; top: 128px; width: 300px; }
  .rule--contact { left: 52px; top: 244px; width: 360px; }
  .address {
    position: absolute; right: 40px; top: 222px;
    text-align: right; font-size: 16px; line-height: 23px;
  }
  .contacts {
    position: absolute; left: 56px; top: 256px;
    list-style: none; font-size: 17px; line-height: 24px;
  }
  .contacts li { display: flex; align-items: center; gap: 8px; }
  .contacts svg { width: 12px; height: 12px; fill: none; stroke: var(--green); stroke-width: 2; }
  .swoosh { position: absolute; left: 0; bottom: 0; width: 700px; height: 100px; }
</style>
</head>
<body>

<section class="card card--back" aria-label="Card back: services">
  <ul class="services">
    <li>Kitchen Renovations</li>
    <li>Bathroom Renovations</li>
    <li>House Renovations</li>
    <li>Garage Conversions</li>
    <li>Extensions</li>
    <li>Loft Conversions</li>
    <li>Conservatories</li>
    <li>Carpentry</li>
    <li>Tiling</li>
    <li>Electrical</li>
    <li>Plumbing &amp; Heating</li>
    <li>Bricklaying</li>
    <li>Landscaping</li>
    <li>Decorating</li>
    <li>Plastering</li>
  </ul>
  <div class="brand">
    <div class="brand__name">VARKELT</div>
    <div class="brand__sub">CONSTRUCTION LTD</div>
  </div>
</section>

<section class="card card--front" aria-label="Card front: contact details">
  <div class="tab"></div>
  <div class="person">
    <div class="person__name">Tomasz Brelwik</div>
    <div class="person__title">Managing Director</div>
  </div>
  <div class="rule rule--name"></div>
  <div class="brand">
    <div class="brand__name">VARKELT</div>
    <div class="brand__sub">CONSTRUCTION LTD</div>
  </div>
  <div class="address">14-16 Harlow Street,<br>London, N4 2QT</div>
  <div class="rule rule--contact"></div>
  <ul class="contacts">
    <li><svg viewBox="0 0 12 12"><path d="M2 1 L4.5 1 L5.5 4 L4 5 Q5 7.5 7 8 L8 6.5 L11 7.5 L11 10 Q6 11 2 6 Q1 3.5 2 1Z"/></svg>020 5194 6281</li>
    <li><svg viewBox="0 0 12 12"><rect x="3" y="1" width="6" height="10" rx="1"/></svg>07845139072</li>
    <li><svg viewBox="0 0 12 12"><rect x="1" y="2.5" width="10" height="7"/><path d="M1 2.5 L6 7 L11 2.5"/></svg>tomasz@varkelt.co.uk</li>
    <li><svg viewBox="0 0 12 12"><circle cx="6" cy="6" r="5"/><path d="M1 6 H11 M6 1 Q3 6 6 11 M6 1 Q9 6 6 11"/></svg>www.varkelt.co.uk</li>
  </ul>
  <svg class="swoosh" viewBox="0 0 700 100" preserveAspectRatio="none" aria-hidden="true">
    <path d="M0 100 L0 88 L440 88 Q470 88 490 60 Q510 30 550 30 L700 30 L700 100 Z" fill="#4c9c3e"/>
    <path d="M0 76 L430 76 Q458 76 476 52 L480 55 Q460 81 432 81 L0 81 Z" fill="#5fb544"/>
  </svg>
</section>

</body>
</html>
```